Venture Capital firm needs modern business cards

We are a Venture Capital firm within financial services/Asset management. The industry generally has basic business cards with black, blue and maybe green/yellow design elements.
Our firm has a four-colour swoosh logo. We are based in London and want to stand out, just a little bit!, from the crowd. Our company is called LORV Investments and the 'C' stands for collaboration thus using makerswarm is a natural portal for our business card design competition. Our logo came via makerswarm too!
We use 'Venture Partner in Asset Management' as our tagline and this is Trademark registered. We operate in a conservative industry and we should not overstep our mark. The logo is colorful as it is and therefore the rest of the design should not be too fanciful.
The objective is twofold: make our logo element stick and memorable with our audience, whilst representing a conservative yet young image.
Updates
The Business Card obviously needs a field for Name, Surname, Job Title, Adress fields: Street, City, Postcode, Country, telefone and cell number, website address, etc.
We have uploaded the ai file. We trust that these are OK. If not, please advise.
Reason: We have have been busy with a client engagement. We will set the project as Guaranteed in return for the troubles we cause. Apologies for the confusion.
Thank you all for these great and creative design suggestions. The team is very happy with a number of your ideas! We will be in touch tomorrow to give individual feedback before the project closes on Friday. We look forward to working with some of you to narrow down your creations. Thank you, LORV Investments team.
All,
Target Market(s)
Financial Services Professionals, Investors, Media, 35-70 years, mainly male, well educated
Industry/Entity Type
Conservative
Requirements
Must have
- We must make use of our logo and potential tagline 'Venture Partner in Asset Management' as we are establishing a new Brand and new company in the market.
We can use 'LORV', 'LORV Investments', and 'LORV Investments'+tagline 'Venture Partner in Asset Management' or simply the four-colour swoosh plus the name of the company as part of the text. (see files)
All design elements are available in black or grey-scale if required. (grey scale swoosh attached).
Due to regulation we must have the following wording on the card in small print 'LORV Investments is an Appointed Representative of Bramwell Holdings Partnership Limited, which is authorised by the Monetary Oversight Board'.
Nice to have
- We would consider designs that make use of different printing techniques such embossing/debossing, UV spot etc.
We attach our colour palette in the files section for your reference.
Should not have
- The font we use for our company name is 'EXO' so do not use a font style that clashes with the corporate fonts, please.
Do not use other design elements than the ones we provide in the file library as part of this project.

```html
<!DOCTYPE html>
<html lang="en">
<head>
<meta charset="utf-8">
<title>LORV Investments – Business Cards</title>
<link href="https://fonts.googleapis.com/css2?family=Exo:wght@600&family=Arimo:wght@400;700&display=swap" rel="stylesheet">
<style>
  :root {
    --stage: #e8e9eb;
    --card: #ffffff;
    --brand-green: #6cbb45;
    --ink: #3a3a3c;
    --ink-soft: #6b6b6e;
    --fine-print: #a9a9ab;
    --on-green: #ffffff;
    --mark: #6cbb45;
  }
  * { box-sizing: border-box; margin: 0; padding: 0; }
  html, body { width: 1200px; height: 514px; overflow: hidden; }
  body {
    background: var(--stage);
    font-family: "Arimo", Arial, sans-serif;
    position: relative;
  }
  .card {
    position: absolute;
    top: 107px;
    width: 520px;
    height: 300px;
    background: var(--card);
    box-shadow: 0 10px 18px rgba(0,0,0,0.18);
  }
  .card--front { left: 50px; }
  .card--back { left: 630px; }

  .brand {
    position: absolute;
    left: 30px;
    top: 28px;
    display: flex;
    align-items: center;
    gap: 12px;
  }
  .brand__dot {
    width: 46px;
    height: 46px;
    border-radius: 50%;
    background: var(--mark);
  }
  .brand__name {
    font-family: "Exo", sans-serif;
    font-weight: 600;
    font-size: 56px;
    line-height: 1;
    color: var(--ink);
    letter-spacing: 1px;
  }
  .brand__tagline {
    position: absolute;
    left: 88px;
    top: 88px;
    font-size: 10px;
    color: var(--ink);
  }

  .band {
    position: absolute;
    left: 0;
    width: 100%;
    background: var(--brand-green);
    color: var(--on-green);
  }
  .card--front .band { top: 151px; height: 103px; }
  .card--back .band { top: 143px; height: 106px; }

  .holder {
    position: absolute;
    left: 32px;
    top: 28px;
  }
  .holder__name { font-weight: 700; font-size: 20px; }
  .holder__role { font-size: 15px; margin-top: 4px; }

  .contact-list {
    position: absolute;
    list-style: none;
  }
  .card--front .contact-list { left: 238px; top: 12px; }
  .card--back .contact-list { left: 20px; top: 14px; }
  .contact-list li {
    display: flex;
    align-items: center;
    gap: 14px;
    font-size: 16px;
    line-height: 1.2;
  }
  .card--front .contact-list li { height: 29px; }
  .card--back .contact-list li { margin-bottom: 12px; }
  .contact-list svg {
    width: 18px;
    height: 18px;
    flex: none;
    fill: none;
    stroke: var(--on-green);
    stroke-width: 1.5;
  }
  .card--back .contact-list li:first-child { align-items: flex-start; }
  .card--back .contact-list li:first-child svg { margin-top: 10px; }

  .fine-print {
    position: absolute;
    left: 30px;
    right: 30px;
    top: 262px;
    font-size: 9px;
    line-height: 1.3;
    color: var(--fine-print);
  }
</style>
</head>
<body>

  <section class="card card--front" aria-label="Business card front">
    <div class="brand">
      <span class="brand__dot"></span>
      <span class="brand__name">LORV</span>
    </div>
    <p class="brand__tagline">Venture Partner in Asset Management</p>

    <div class="band">
      <div class="holder">
        <p class="holder__name">Daniel Harrow</p>
        <p class="holder__role">Chairman</p>
      </div>
      <ul class="contact-list">
        <li>
          <svg viewBox="0 0 18 18"><rect x="2" y="4" width="14" height="10"/><path d="M2 4l7 6 7-6"/></svg>
          daniel@lorvinvestments.com
        </li>
        <li>
          <svg viewBox="0 0 18 18"><path d="M4 2l3 3-1.5 2a9 9 0 0 0 5.5 5.5L13 11l3 3-2 2C8 16 2 10 2 4z"/></svg>
          +1 (800) 314-7720
        </li>
        <li>
          <svg viewBox="0 0 18 18"><rect x="5" y="1.5" width="8" height="15" rx="1"/><path d="M8 14h2"/></svg>
          +1 (800) 314-7720
        </li>
      </ul>
    </div>
  </section>

  <section class="card card--back" aria-label="Business card back">
    <div class="brand">
      <span class="brand__dot"></span>
      <span class="brand__name">LORV</span>
    </div>
    <p class="brand__tagline">Venture Partner in Asset Management</p>

    <div class="band">
      <ul class="contact-list">
        <li>
          <svg viewBox="0 0 18 18"><path d="M2 9l7-6 7 6"/><path d="M4 8v8h10V8"/><path d="M7.5 16v-4h3v4"/></svg>
          <span>17 Carlow Street, 22 Fenwick Square,<br>London, United Kingdom EC2M 4RT</span>
        </li>
        <li>
          <svg viewBox="0 0 18 18"><circle cx="9" cy="9" r="7"/><ellipse cx="9" cy="9" rx="3" ry="7"/><path d="M2 9h14"/></svg>
          www.lorvinvestments.com
        </li>
      </ul>
    </div>

    <p class="fine-print">‘LORV Investments is an Appointed Representative of Bramwell Holdings Partnership Limited, which is authorised by the Monetary Oversight Board’.</p>
  </section>

</body>
</html>
```